Q.B. Brightpath Store

The design is for eCommerce home page but I would like it to complement this site: http://www.qbbrightpathsolutions.com/ but... it should also have independence as a standalone site.

The best design will be able to effectively mix corporate with a high quality small business consumer feel. It should be completely custom design, not a template look or feel. I want the users to get the feeling that this is the place to go for buying tech for business. We sell the same products as RVK.

You can be creative as you wish, as long as the elements of a great eCommerce site are present.

I would like your 'design' to blow these away:
http://www.shopping.zl.com/
mirabelo.com
http://www.rvk.com/

Here are references:
Call to action
http://markvantage.com/us/blog/48153-seven-tips-for-designing-an-effective-ecommerce-call-to-action

Effective Ecommerce design
http://www.vexa.com/ss/7-tips-for-effective-e-commerce#0

91 points of ecommerce
http://qir.com/blog/holygrail-of-ecommerce-conversion-optimization-91-points-checklist

UPDATE 07/11/2013:

Please look at the category sample png files. I see already many people are using the main menu from qbbrightpathsolutions.com and I do not mind your creativiety, but this is an eCommerce store and people need a menu to get to the categories and/or product types. I don't want to limit anyone creativity by the png samples. I'm also not using them to show I like them in any particular way or form, just that it's needed, whether it's a button (dropdown of course) that says 'Categories' or 'Products, whether it an accordion, horizontal or vertical.

Thanks

UPDATE 07/12/2013:

Please find other use of space that has been used for About Us paragraph (if you've added it to the page). About Us should have it's own page and the purpose of the design should be to sell products (and some services as products). Please put a link or some other creative method to lead users to the About Us page.

Reason: I've raised the award, including 1st, 2nd, and 3rd place and participation payments so I will also extend 7 days. Thanks!

I've updated the product brief. Please scroll down to where it says: UPDATE 07/11/2013

Thanks!

UPDATE 07/12/2013:

Please find other use of space that has been used for About Us paragraph (if you've added it to the page).  About Us should have it's own page and the purpose of the design should be to sell products (and some services as products). Please put a link or some other creative method to lead users to the About Us page if you must but not on the real estate of the page.

Thanks!

Added updates to the brief 7/14/2013.

Thanks!

The voting is in and the project is complete.  Thanks everyone for joining, all of those who participated are truly amazingly talented. But, there were only 3 prizes.  I will be having further projects down the line to develop other pages to this site after the initial implementation is completed.  I truly would like to have you all back. 

- Thank you.

Target Market(s)

corporate decision-makers AND small business consumers

Industry/Entity Type

Small Business

Requirements
Must have
• Call to action.
Openness (non-clutter).

These elements:
Search box
Logo
Tagline
Telephone number
Contact details
Address
My account / sign in
Shopping basket / checkout link
Latest offers
Promotional area
Email sign up
Delivery information
About us
Link to press office / corporate site
Terms and conditions
Sitemap for the footer.
Delivery offers: free
Personalized recommendations
Social media links
Accepted payment methods
Link to blog or community section
Change language / country

http://smartplansblog.pelloware.com/sales-leads-landing-page/

UPDATE 07/14/2013
Category Menu. This can be a dropdown, horizontal, vertical, etc. But shoppers need to know how to get to the products they want to buy.
Nice to have
• Trustmarks
Blog/Blog link

UPDATE 07/12/2013:
Make the footer useful.

UPDATE 07/14/2013 (Suggestions of elements to differentiate your designs)

-Quick Shop: A quick buy module/section: Where a user can put in a SKU number or Model number to quickly add the product to their shopping cart.

-Featured
-Best Sellers
-Specials
-Trending Tags/Tag Cloud
- Activity Stream
- Cross Sell/ Up Sell
- Testimonial
- Social Network Feed
- Live Help
- Feedback/Support/Contact Tab
- Show logged in user (i.e. Welcome, Mark Pelley)
Should not have
• The design SHOULD NOT be generic like this:

http://www.artgatherly.com/design/52392
http://www.falconmart.com/

The page should not feel over cluttered. It should not have low quality icons or design elements. Navigation should not be hard to discover or confusing.

```html
<!DOCTYPE html>
<html lang="en">
<head>
<meta charset="utf-8">
<title>Q.B. Brightpath Store</title>
<link href="https://fonts.googleapis.com/css2?family=Open+Sans:wght@400;600;700;800&display=swap" rel="stylesheet">
<style>
:root{
  --navy:#0f2b57;
  --blue:#1d63b5;
  --blue-light:#3d8ad8;
  --sky:#e6f1fb;
  --red:#c8302a;
  --ink:#333840;
  --muted:#6d737b;
  --line:#d9dde2;
  --panel:#f1f2f4;
  --card:#4a4e55;
  --footer:#3d4046;
  --footer-dark:#2c2f33;
  --white:#ffffff;
}
*{box-sizing:border-box;margin:0;padding:0}
html,body{width:898px;height:1200px;overflow:hidden}
body{font-family:"Open Sans",Arial,sans-serif;color:var(--ink);background:var(--white);position:relative;font-size:9px}
.abs{position:absolute}
a{color:inherit;text-decoration:none}

.topbar{left:0;top:0;width:898px;height:20px;background:var(--navy);color:#c9d6ea;font-size:7.5px;font-weight:600}
.topbar .links{position:absolute;left:520px;top:6px;letter-spacing:.3px}
.topbar .links span{margin:0 5px}
.lang{position:absolute;left:770px;top:3px;width:82px;height:14px;background:var(--white);color:var(--ink);border-radius:2px;font-size:7.5px;padding:2px 4px 0 20px}
.lang i{position:absolute;left:4px;top:3px;width:12px;height:8px;background:var(--blue)}

.brand{left:48px;top:38px;display:flex;align-items:center;gap:8px;color:var(--blue);font-weight:800;font-size:19px;letter-spacing:.2px}
.brand i{width:34px;height:34px;border-radius:50%;background:var(--blue)}
.header-tools{left:640px;top:28px;width:214px;font-size:8px;color:var(--muted)}
.cart-row{display:flex;justify-content:space-between;align-items:center}
.cart-row b{color:var(--blue);font-weight:600}
.search{margin-top:-12px;margin-left:100px;width:114px;height:15px;border:1px solid var(--line);border-radius:2px;padding:2px 4px;font-size:7px;color:#9aa0a6}
.contact{margin-top:8px;margin-left:100px;line-height:13px;font-size:7.5px}
.contact b{color:var(--red)}

.nav{left:45px;top:100px;width:810px;height:26px;background:linear-gradient(var(--blue-light),var(--blue));display:flex;justify-content:space-around;align-items:center;color:var(--white);font-weight:700;font-size:8.5px;letter-spacing:.4px}

.hero{left:45px;top:126px;width:810px;height:290px;background:linear-gradient(100deg,var(--white) 40%,var(--sky))}
.hero h1{position:absolute;left:24px;top:42px;width:300px;font-size:22px;line-height:28px;font-weight:800;color:var(--blue);text-transform:uppercase}
.hero .tag{position:absolute;left:24px;top:140px;width:240px;font-size:10px;line-height:14px;font-weight:700;color:var(--red);text-transform:uppercase}
.hero .cta{position:absolute;top:198px;height:20px;padding:5px 10px;font-size:8px;font-weight:700;border-radius:2px;background:var(--panel);border:1px solid var(--line);color:var(--navy)}
.hero .photo{position:absolute;left:420px;top:14px;width:370px;height:250px;background:linear-gradient(160deg,#f4f7fa,#c7d3de 60%,#8a96a3)}
.dots{position:absolute;left:395px;top:272px;display:flex;gap:5px}
.dots i{width:7px;height:7px;border-radius:50%;background:#b9c4d0}
.dots i:first-child{background:var(--blue)}

.feature{top:430px;height:68px;background:var(--panel);border:1px solid var(--line);border-radius:3px}
.feature h3{font-size:10px;font-weight:800;color:var(--navy);text-transform:uppercase;line-height:13px}
.feature p{font-size:7px;color:var(--muted);line-height:10px}
.f-delivery{left:45px;width:255px}
.f-delivery svg{position:absolute;left:14px;top:18px}
.f-delivery h3{position:absolute;left:82px;top:22px}
.f-email{left:315px;width:270px}
.f-email h3{position:absolute;left:90px;top:12px}
.f-email svg{position:absolute;left:60px;top:11px}
.f-email .field{position:absolute;left:20px;top:36px;width:200px;height:18px;background:var(--white);border:1px solid var(--line);font-size:7px;color:#9aa0a6;padding:4px 6px}
.f-email .go{position:absolute;left:226px;top:36px;width:26px;height:18px;background:var(--blue);color:var(--white);font-weight:700;font-size:7.5px;text-align:center;padding-top:4px}
.f-blog{left:600px;width:255px}
.f-blog i{position:absolute;left:18px;top:14px;width:38px;height:38px;border-radius:50%;background:var(--blue)}
.f-blog h3{position:absolute;left:120px;top:12px}
.f-blog p{position:absolute;left:118px;top:30px;width:120px}

.section-title{font-size:10.5px;font-weight:800;color:var(--navy);text-transform:uppercase}
.para{font-size:7.5px;line-height:11px;color:var(--muted)}
.welcome{left:45px;top:515px;width:810px}
.welcome .para{margin-top:6px}
.rule{left:45px;width:810px;height:1px;background:var(--line)}

.solutions{left:45px;top:598px;width:165px}
.solutions ul{list-style:none;margin-top:8px}
.solutions li{font-size:7.5px;line-height:13px;color:var(--ink);border-bottom:1px dotted var(--line)}
.btn{display:inline-block;background:var(--blue);color:var(--white);font-weight:700;font-size:7px;padding:3px 7px;border-radius:2px}
.solutions .btn{margin-top:10px}

.offers{left:225px;top:598px;width:630px}
.cards{display:flex;gap:10px;margin-top:10px}
.card{width:150px;height:168px;background:var(--panel);border:1px solid var(--line);position:relative}
.card .shot{position:absolute;left:10px;top:10px;width:128px;height:84px;background:linear-gradient(#dfe6ee,#9fb0c2)}
.card .name{position:absolute;left:0;top:102px;width:148px;text-align:center;font-size:7.5px;font-weight:600}
.card .price{position:absolute;left:10px;top:136px;font-size:8px;font-weight:700;color:var(--red)}
.card .btn{position:absolute;right:10px;top:133px}

.about{left:45px;top:808px;width:590px}
.about .para{margin-top:6px}
.payments{left:660px;top:805px;width:195px;height:62px;border:1px solid var(--line)}
.payments h4{background:var(--navy);color:var(--white);font-size:8.5px;font-weight:800;padding:4px 8px;text-transform:uppercase}
.payments .methods{display:flex;gap:8px;padding:10px 10px}
.payments .methods i{width:38px;height:22px;border-radius:3px;background:#c4cad2}

.footer{left:0;top:880px;width:898px;height:300px;background:var(--footer);color:#c3c7cc}
.fcols{position:absolute;left:45px;width:810px;display:flex}
.fcol{width:200px}
.fcol h5{color:var(--white);font-size:8.5px;font-weight:800;text-transform:uppercase;margin-bottom:6px}
.fcol p{font-size:7.5px;line-height:12px}
.fcol .social{display:flex;gap:5px;margin-top:6px}
.fcol .social i{width:14px;height:14px;border-radius:50%;background:#6a6f76}
.account .field{width:160px;height:15px;background:#55595f;margin-bottom:5px;font-size:7px;padding:3px 5px;color:#a9aeb4}
.fbottom{left:0;top:1180px;width:898px;height:20px;background:var(--footer-dark);color:#a4a9af;font-size:7px;text-align:right;padding:6px 45px 0 0}
</style>
</head>
<body>

<div class="abs topbar">
  <div class="links"><span>MY ACCOUNT</span>|<span>ABOUT US</span>|<span>CHECKOUT</span>|<span>SIGN IN</span></div>
  <div class="lang"><i></i>English ▾</div>
</div>

<div class="abs brand"><i></i>Q.B. BRIGHTPATH</div>

<div class="abs header-tools">
  <div class="cart-row"><span><b>View your cart</b> | Checkout</span></div>
  <div class="search">Search products...</div>
  <div class="contact">
    <div><b>Call Us:</b> 1 (555) 014-2200</div>
    <div><b>Email:</b> info@qbbrightpathsolutions.com</div>
  </div>
</div>

<nav class="abs nav">
  <a>HOME</a><a>HARDWARE</a><a>SOFTWARE</a><a>IT RESOURCE</a><a>TECHNOLOGY</a>
</nav>

<section class="abs hero">
  <h1>From single owned to medium size, we got you covered</h1>
  <p class="tag">Our business technology analyst and advocacy consulting stand beside you</p>
  <a class="cta" style="left:24px">VIRTUAL MARKETS</a>
  <a class="cta" style="left:122px">TOP SOLUTIONS</a>
  <div class="photo" role="img" aria-label="Photo of a business woman working on a laptop at a desk"></div>
  <div class="dots"><i></i><i></i><i></i><i></i></div>
</section>

<div class="abs feature f-delivery">
  <svg width="56" height="32" viewBox="0 0 56 32"><rect x="1" y="4" width="34" height="20" fill="#1d63b5"/><path d="M35 10h12l7 8v6H35z" fill="#0f2b57"/><circle cx="12" cy="27" r="4" fill="#333840"/><circle cx="45" cy="27" r="4" fill="#333840"/></svg>
  <h3>Delivery offers<br>business initiatives</h3>
</div>

<div class="abs feature f-email">
  <svg width="22" height="15" viewBox="0 0 22 15"><rect x="1" y="1" width="20" height="13" fill="#fff" stroke="#1d63b5" stroke-width="1.5"/><path d="M1 1l10 8 10-8" fill="none" stroke="#1d63b5" stroke-width="1.5"/></svg>
  <h3>Email sign up</h3>
  <div class="field">Enter your email here...</div>
  <div class="go">GO</div>
</div>

<div class="abs feature f-blog">
  <i></i>
  <h3>Our blog</h3>
  <p>Fresh tech notes from our team and weekly business buying tips.</p>
</div>

<section class="abs welcome">
  <h2 class="section-title">Welcome to our company</h2>
  <p class="para">At Q.B. Brightpath we help growing businesses choose, buy and manage the right technology. From laptops and servers to licensing and support plans, our specialists compare options, explain the trade-offs and deliver gear that works from day one. Shop with confidence, backed by free delivery on qualifying orders and friendly advice.</p>
</section>
<div class="abs rule" style="top:590px"></div>

<section class="abs solutions">
  <h2 class="section-title">Top Solutions</h2>
  <ul>
    <li>B2B Solutions</li><li>Cloud Solutions</li><li>Email and Messaging</li><li>Hardware Maintenance</li><li>IT Services</li><li>Managed IT Support</li><li>Software Licensing</li><li>Mobility</li><li>Solid State Technology</li>
  </ul>
  <a class="btn">VIEW ALL</a>
</section>

<section class="abs offers">
  <h2 class="section-title">Latest Offers</h2>
  <div class="cards">
    <div class="card"><div class="shot" role="img" aria-label="Product photo of a tablet"></div><div class="name">Solvane tab 10.1</div><div class="price">$ 499.99</div><a class="btn">SHOP NOW</a></div>
    <div class="card"><div class="shot" role="img" aria-label="Product photo of a touchscreen laptop"></div><div class="name">Lightweight Touchscreen laptops</div><div class="price">$ 899.99</div><a class="btn">SHOP NOW</a></div>
    <div class="card"><div class="shot" role="img" aria-label="Product photo of networking equipment"></div><div class="name">Wireless Network Kits</div><div class="price">$ 299.99</div><a class="btn">SHOP NOW</a></div>
    <div class="card"><div class="shot" role="img" aria-label="Product photo of an all in one computer"></div><div class="name">All in one touch pc</div><div class="price">$ 999.99</div><a class="btn">SHOP NOW</a></div>
  </div>
</section>

<section class="abs about">
  <h2 class="section-title">About Us</h2>
  <p class="para">We are a team of technology buyers and support engineers serving small and mid-size firms. We stock the brands you trust, price them fairly and stand behind every order with setup help and clear warranty support. Learn more about our story and the people behind the store.</p>
</section>

<div class="abs payments">
  <h4>Payment methods</h4>
  <div class="methods"><i></i><i></i><i></i><i></i></div>
</div>

<footer class="abs footer">
  <div class="fcols" style="top:18px">
    <div class="fcol"><h5>Our Company</h5><p>About Us<br>Careers<br>Corporate<br>Partners</p><div class="social"><i></i><i></i><i></i><i></i></div></div>
    <div class="fcol"><h5>Main Menu</h5><p>Home<br>Hardware<br>Software<br>IT Resource<br>Technology</p></div>
    <div class="fcol"><h5>User Menu</h5><p>My Account<br>My Orders<br>Wish List<br>Checkout<br>Sign In</p></div>
    <div class="fcol account"><h5>My Account</h5><div class="field">Username</div><div class="field">Password</div><a class="btn">LOGIN</a></div>
  </div>
  <div class="fcols" style="top:150px">
    <div class="fcol"><h5>Our Location</h5><p>214 Harbor Lane, Suite 5<br>Riverton, CA 90210<br>United States</p></div>
    <div class="fcol"><h5>Products and Services</h5><p>Business Hardware<br>Software Licensing<br>Managed Services<br>Cloud Plans</p></div>
    <div class="fcol"><h5>Programs</h5><p>Terms &amp; Conditions<br>Delivery Info<br>Press Office<br>Sitemap</p></div>
    <div class="fcol"><h5>Contact Us</h5><p>Call Us: 1 (555) 014-2200<br>Email: info@qbbrightpathsolutions.com<br>Live Help</p></div>
  </div>
</footer>
<div class="abs fbottom">Copyright © 2013 Q.B. Brightpath Store. All rights reserved.</div>

</body>
</html>
```